TuneRoost - Music Industry App needs a top quality wordpress homepage

We need a modern responsive wordpress homepage built. Our website will only feature one page with the goal to get people to sign up to our app. A word document has been uploaded outlining the page content/sections.

Once the homepage is finalised, I will also need 2 landing pages built as part of this competition. It will be very similar to the homepage with the same layout etc but just feature different images and content. The homepage is for anyone (artists and venues) to find out about us but the landing pages will be artist or venue specific.

The completed work must be delivered as an exportable file into wordpress and be designed properly so no more work is needed to begin utilising as the actual website. The images used must be setup correctly for speed and quality also.

Target Market(s)

Venues and Artists.

Coding

Coded - Design and coding required

Requirements
Must have
• UPDATE: High Res Logo files attached
• Must be a modern looking website and be responsive. Must look good across all devices from desktop, to mobile and tablet. Needs to be very high quality.
• Please see the attached logo - I am waiting for the final high quality version and will reupload when complete but this will be enough to get you started for now. The website must have a dark base colour and have red/white elements to match the logo. The red colour used MUST match the red colour used in the logo.
• Please have a go at creating it how you think is best and provide feedback from there. I am leaving it very open to the designers so I can get the best website possible and lots of different ideas etc.

```html
<!DOCTYPE html>
<html lang="en">
<head>
<meta charset="utf-8">
<title>TuneRoost – Live Music Booking</title>
<link href="https://fonts.googleapis.com/css2?family=Red+Hat+Display:wght@400;500;700;900&family=Lato:wght@300;400;700&display=swap" rel="stylesheet">
<style>
:root{
  --red:#d9001b;
  --dark:#15161d;
  --ink:#333;
  --muted:#666;
  --card:#e5e5e5;
  --field:#e8e8e8;
  --white:#fff;
}
*{box-sizing:border-box;margin:0;padding:0}
html,body{width:1200px;height:3515px;overflow:hidden}
body{font-family:"Lato",sans-serif;color:var(--ink);background:var(--white);position:relative}
.page{position:relative;width:1200px;height:3515px;overflow:hidden}
.backdrop{position:absolute;left:0;top:0}
.abs{position:absolute}
h1,h2,h3{font-family:"Red Hat Display",sans-serif}
.center{left:0;width:1200px;text-align:center}

/* hero */
.brand{top:16px;left:0;width:1200px;text-align:center;color:var(--white);font-family:"Red Hat Display",sans-serif;font-weight:500;font-size:32px}
.brand-dot{display:block;width:46px;height:46px;margin:0 auto 6px;border-radius:50%;border:5px solid var(--white)}
.menu-btn{left:992px;top:15px;width:40px;height:40px;border:2px solid var(--white);border-radius:50%}
.menu-btn i{position:absolute;left:12px;width:13px;height:2px;background:var(--white)}
.hero-title{top:124px;font-size:35px;font-weight:900;color:var(--white)}
.hero-sub{top:164px;font-size:19px;color:var(--white);font-weight:400}
.hero-cta{top:268px;font-size:20px;color:var(--white);font-weight:500;font-family:"Red Hat Display",sans-serif}
.signup{display:flex;height:38px}
.signup .field{background:var(--white);font-size:11px;color:#555;padding:0 15px;display:flex;align-items:center}
.signup .btn{background:var(--red);color:var(--white);font-family:"Red Hat Display",sans-serif;font-weight:500;font-size:17px;display:flex;align-items:center;justify-content:center}
.hero-signup{left:440px;top:302px}
.hero-signup .field{width:232px}
.hero-signup .btn{width:87px}
.arrow{top:292px;width:24px;height:30px}

/* how it works */
.section-title{font-size:34px;font-weight:500}
.how-title{top:764px;color:var(--red)}
.steps{left:144px;top:846px;display:flex;gap:8px}
.step{position:relative;width:177px;height:194px;background:var(--card);border-top:3px solid #444;text-align:center}
.step-num{position:absolute;left:67px;top:-24px;width:42px;height:42px;border-radius:50%;background:#333;color:var(--white);font-size:16px;line-height:42px;font-weight:700}
.step svg{margin-top:38px;width:60px;height:60px}
.step p{font-size:12.5px;line-height:17.5px;color:#555;padding:6px 18px 0}

/* why */
.why-title{top:1272px;color:var(--white);font-weight:700}
.features{left:144px;top:1345px;display:flex}
.feature{width:237px;color:var(--white)}
.feature svg{width:58px;height:58px}
.feature h3{font-size:33px;font-weight:500;margin-top:2px}
.feature p{font-size:11.5px;line-height:17.5px;margin-top:6px;padding-right:24px}

/* audiences */
.divider{left:599px;top:1731px;width:1px;height:390px;background:#ccc}
.audience{top:1731px;width:420px}
.audience h2{font-size:34px;color:var(--red);font-weight:500;margin-top:10px}
.audience ul{list-style:none;margin-top:12px}
.audience li{font-size:10.5px;line-height:24px;color:#444;padding-left:11px;position:relative}
.audience li::before{content:"";position:absolute;left:0;top:11px;width:4px;height:4px;border-radius:50%;background:#444}
.audience .note{font-size:11.5px;line-height:19px;color:#444;margin-top:9px}
.audience .signup{margin-top:28px}
.audience .signup .field{width:232px;background:var(--field)}
.audience .signup .btn{width:88px}

/* about */
.about-title{top:2378px;color:var(--white)}
.about-text{left:143px;top:2432px;width:914px;text-align:center;font-size:12px;line-height:25px;color:#ddd}

/* contact */
.contact-title{font-size:34px;color:var(--red);font-weight:500}
.info{left:143px;top:2856px;list-style:none}
.info li{font-size:13px;color:#444;height:32px;display:flex;align-items:center;gap:12px}
.info svg{width:11px;height:11px}
.map{left:143px;top:2973px;width:359px;height:276px;background:linear-gradient(135deg,#e4e6e8,#d5d9dc 55%,#b9d78d)}
.form{left:695px;top:2861px;width:360px}
.form .input{background:var(--field);height:47px;font-size:12.5px;color:#888;padding:16px 15px;margin-bottom:9px}
.form .message{height:151px}
.verify{left:695px;top:3191px;width:241px;height:58px;border:1px solid #ddd;background:#f9f9f9;box-shadow:0 1px 3px rgba(0,0,0,.12)}
.verify .box{position:absolute;left:10px;top:19px;width:21px;height:21px;border:2px solid #bbb;background:var(--white);border-radius:2px}
.verify span{position:absolute;left:41px;top:21px;font-size:11px;color:#333}
.verify .mark{position:absolute;right:12px;top:14px;width:28px;height:28px;border-radius:50%;background:#c8d2e6}
.submit{left:968px;top:3201px;width:87px;height:37px;background:var(--red);color:var(--white);font-family:"Red Hat Display",sans-serif;font-weight:500;font-size:16px;display:flex;align-items:center;justify-content:center}

/* footer */
.footer-nav{left:144px;top:3430px;font-size:10.5px;color:#aaa}
.footer-nav span{margin:0 7px;color:#777}
.copyright{left:144px;top:3462px;font-size:10.5px;color:#aaa}
.social{left:925px;top:3447px;display:flex;gap:24px}
.social i{display:block;width:14px;height:14px;border-radius:50%;background:#8a8c93}
</style>
</head>
<body>
<div class="page">

<svg class="backdrop" width="1200" height="3515" viewBox="0 0 1200 3515">
  <defs>
    <radialGradient id="concertGlow" cx="0.55" cy="0.3" r="0.8">
      <stop offset="0" stop-color="#c46a34"/>
      <stop offset="0.45" stop-color="#6a2e1c"/>
      <stop offset="1" stop-color="#1d100d"/>
    </radialGradient>
    <linearGradient id="stageNight" x1="0" y1="0" x2="1" y2="1">
      <stop offset="0" stop-color="#22232d"/>
      <stop offset="0.55" stop-color="#3a3540"/>
      <stop offset="1" stop-color="#16171e"/>
    </linearGradient>
    <linearGradient id="crowdNight" x1="0" y1="0" x2="0" y2="1">
      <stop offset="0" stop-color="#2a2c36"/>
      <stop offset="1" stop-color="#121318"/>
    </linearGradient>
  </defs>

  <g role="img" aria-label="Photo of a concert crowd with raised hands under warm stage lights">
    <polygon points="0,0 1200,0 1200,632 0,694" fill="url(#concertGlow)"/>
  </g>
  <polygon points="0,690 1200,614 1200,642 0,700" fill="var(--red)"/>

  <g role="img" aria-label="Photo of an outdoor festival stage at night">
    <polygon points="0,1184 1200,1122 1200,1574 0,1649" fill="url(#stageNight)"/>
  </g>
  <polygon points="0,1176 1200,1130 1200,1135 0,1200" fill="var(--red)"/>
  <polygon points="0,1643 1200,1570 1200,1596 0,1650" fill="var(--red)"/>

  <g role="img" aria-label="Photo of a crowd facing a lit stage at night">
    <polygon points="0,2282 1200,2202 1200,2656 0,2730" fill="url(#crowdNight)"/>
  </g>
  <polygon points="0,2274 1200,2206 1200,2211 0,2296" fill="var(--red)"/>
  <polygon points="0,2724 1200,2647 1200,2672 0,2730" fill="var(--red)"/>

  <polygon points="0,3394 1200,3318 1200,3515 0,3515" fill="var(--dark)"/>
  <polygon points="0,3386 1200,3318 1200,3324 0,3406" fill="var(--red)"/>
</svg>

<!-- hero -->
<div class="abs brand"><span class="brand-dot"></span>TuneRoost</div>
<div class="abs menu-btn"><i style="top:13px"></i><i style="top:18px"></i><i style="top:23px"></i></div>
<h1 class="abs center hero-title">RIDELINE FOR LIVE MUSIC</h1>
<p class="abs center hero-sub">TuneRoost connects venues with artists to make booking gigs simple</p>
<p class="abs center hero-cta">Sign up now for FREE</p>
<div class="abs signup hero-signup"><div class="field">Enter E-mail Address</div><div class="btn">SIGN UP</div></div>
<svg class="abs arrow" style="left:52px" viewBox="0 0 24 30"><polyline points="17,4 6,15 17,26" fill="none" stroke="#fff" stroke-width="4"/></svg>
<svg class="abs arrow" style="left:1122px" viewBox="0 0 24 30"><polyline points="7,4 18,15 7,26" fill="none" stroke="#fff" stroke-width="4"/></svg>

<!-- how it works -->
<h2 class="abs center section-title how-title">How TuneRoost Works</h2>
<div class="abs steps">
  <div class="step"><div class="step-num">1</div>
    <svg viewBox="0 0 60 60" fill="none" stroke="#222" stroke-width="2"><rect x="6" y="4" width="36" height="50"/><circle cx="24" cy="18" r="6"/><path d="M15 32h18M15 38h18M15 44h12"/><path d="M50 18l6 6-20 24-8 2 2-8z"/></svg>
    <p>Artists and venues sign up for free and create a profile</p></div>
  <div class="step"><div class="step-num">2</div>
    <svg viewBox="0 0 60 60" fill="none" stroke="#222" stroke-width="2"><circle cx="36" cy="22" r="16"/><circle cx="36" cy="22" r="11"/><path d="M24 34L6 54"/></svg>
    <p>Venues search for an artist for their upcoming gigs</p></div>
  <div class="step"><div class="step-num">3</div>
    <svg viewBox="0 0 60 60" fill="none" stroke="#222" stroke-width="2"><path d="M24 20l26 12-11 4 9 13-5 4-9-13-6 9z"/><path d="M10 14l6 5M20 6v7M8 26h7M28 10l-4 4"/></svg>
    <p>Venues request a quote and communicate with the artist direct</p></div>
  <div class="step"><div class="step-num">4</div>
    <svg viewBox="0 0 60 60" fill="none" stroke="#222" stroke-width="2"><rect x="10" y="4" width="40" height="52"/><rect x="16" y="10" width="28" height="6"/><circle cx="24" cy="26" r="4"/><path d="M17 38c0-5 14-5 14 0M34 24h10M34 30h10M17 44h27M17 50h27"/></svg>
    <p>The gig is booked in once payment is provided by the venue.</p></div>
  <div class="step"><div class="step-num">5</div>
    <svg viewBox="0 0 60 60" fill="none" stroke="#222" stroke-width="2"><circle cx="30" cy="30" r="26"/><path d="M18 31l8 8 17-18"/></svg>
    <p>Upon completion the money is paid to the artist within 48 hours or less.</p></div>
</div>

<!-- why -->
<h2 class="abs center section-title why-title">Why TuneRoost?</h2>
<div class="abs features">
  <div class="feature">
    <svg viewBox="0 0 58 58" fill="none" stroke="#fff" stroke-width="2"><circle cx="22" cy="22" r="12" stroke-dasharray="5 3"/><circle cx="22" cy="22" r="6"/><circle cx="42" cy="42" r="9" stroke-dasharray="4 3"/><circle cx="42" cy="42" r="4"/></svg>
    <h3>Simple</h3><p>TuneRoost makes gig booking easy for both the venue and artist</p></div>
  <div class="feature">
    <svg viewBox="0 0 58 58" fill="none" stroke="#fff" stroke-width="2"><circle cx="29" cy="16" r="8"/><path d="M15 50V36c0-6 28-6 28 0v14"/><circle cx="10" cy="26" r="6"/><path d="M2 50V40c0-4 8-5 12-4"/><circle cx="48" cy="26" r="6"/><path d="M56 50V40c0-4-8-5-12-4"/></svg>
    <h3>Connect</h3><p>Join the TuneRoost community which is full of amazing artists and venues.</p></div>
  <div class="feature">
    <svg viewBox="0 0 58 58" fill="none" stroke="#fff" stroke-width="2"><path d="M17 24V16a12 12 0 0 1 24 0v8"/><rect x="10" y="24" width="38" height="30" rx="5"/><rect x="24" y="32" width="10" height="14" rx="5"/></svg>
    <h3>Protection</h3><p>Everyone is protected with our complimentary dispute resolutions.</p></div>
  <div class="feature">
    <svg viewBox="0 0 58 58" fill="none" stroke="#fff" stroke-width="2"><path d="M30 8h16v16L22 50 6 34z"/><circle cx="40" cy="15" r="3"/><path d="M42 12l12-10"/></svg>
    <h3>Price</h3><p>Get the best rate possible with TuneRoost only receiving 5% of the artists fee.</p></div>
</div>

<!-- venues / artists -->
<div class="abs divider"></div>
<div class="abs audience" style="left:143px">
  <svg width="82" height="82" viewBox="0 0 82 82" fill="none" stroke="var(--red)" stroke-width="2.5"><path d="M41 62C26 44 20 34 20 24a21 21 0 0 1 42 0c0 10-6 20-21 38z"/><circle cx="41" cy="24" r="8"/><path d="M26 56C10 58 2 62 2 68c0 7 18 12 39 12s39-5 39-12c0-6-8-10-24-12"/></svg>
  <h2>Venues</h2>
  <ul>
    <li>TuneRoost is a 100% FREE service for all venues - you pay us nothing!</li>
    <li>Get instant access to hundreds of artists around your local community</li>
    <li>All genres to suit any venue from a pub to a wedding or even a nightclub</li>
    <li>Simple booking process with a money back guarantee</li>
    <li>Communicate directly with the artist and negotiate the price</li>
  </ul>
  <p class="note">TuneRoost is not yet ready to host gigs as we're currently working on building our artists. We are launching for venues in Q4 2019. Pre-register now to keep informed and be one of the first people to use our platform.</p>
  <div class="signup"><div class="field">Enter E-mail Address</div><div class="btn">SIGN UP</div></div>
</div>
<div class="abs audience" style="left:657px">
  <svg width="82" height="82" viewBox="0 0 82 82" fill="none" stroke="var(--red)" stroke-width="2.5"><rect x="30" y="6" width="22" height="36" rx="11"/><path d="M22 32a19 19 0 0 0 38 0M41 51v16M28 76h26"/><path d="M10 40V20l10-3v18"/><circle cx="7" cy="40" r="3"/><path d="M72 36V14"/><circle cx="69" cy="36" r="3"/></svg>
  <h2>Artists</h2>
  <ul>
    <li>Sign up to TuneRoost for FREE and get yourself in front of venues</li>
    <li>Only pay us if you get a gig - we only get 5% of the fee you charge the venue</li>
    <li>All genres and artists welcome - as long as you're experienced and professional</li>
    <li>Get paid within 48 hours or less after the gig guaranteed!</li>
    <li>Negotiate your price and don't pay huge agent fees to ensure you earn top dollar</li>
  </ul>
  <p class="note">Sign up and create your TuneRoost profile now</p>
  <div class="signup"><div class="field">Enter E-mail Address</div><div class="btn">SIGN UP</div></div>
</div>

<!-- about -->
<h2 class="abs center section-title about-title">About TuneRoost</h2>
<p class="abs about-text">Vestibulum condimentum, risus ut posuere cursus, velit justo accumsan sem, lobortis aliquet metus dui eu libero. Pellentesque a imperdiet dolor, et auctor est. Fusce sollicitudin lorem et luctus volutpat. Proin placerat dapibus gravida. In tristique tristique nulla eget hendrerit. Maecenas vel tortor accumsan quam varius imperdiet vel eget elit. Aenean facilisis tincidunt lectus, id dictum nisi luctus eget. Vivamus efficitur ex condimentum, malesuada eros eget, feugiat nibh. Sed tellus ex, imperdiet eget gravida sit amet, volutpat eget turpis. In nec ultricies est. Etiam mattis augue vehicula odio posuere, sit amet tempus lectus luctus. Nulla facilisi. Etiam vel massa elementum, bibendum tellus venenatis, feugiat massa. Curabitur venenatis lacinia ornare. Cras sollicitudin cursus dui eu placerat.</p>

<!-- contact -->
<h2 class="abs contact-title" style="left:143px;top:2802px">Contact Info</h2>
<div class="abs" style="left:599px;top:2818px;width:1px;height:430px;background:#ccc"></div>
<ul class="abs info">
  <li><svg viewBox="0 0 11 11"><path d="M5.5 11C2 7 1.5 5.5 1.5 4a4 4 0 0 1 8 0c0 1.5-.5 3-4 7z" fill="#333"/></svg>18 Harbour Lane, Eastgate, Townsville 4021</li>
  <li><svg viewBox="0 0 11 11"><path d="M2 1l2 0 1 3-1.5 1a6 6 0 0 0 2.5 2.5L7 6l3 1v2c0 1-1 1-1 1A9 9 0 0 1 1 2s0-1 1-1z" fill="#333"/></svg>Phone : 555 014 2290</li>
  <li><svg viewBox="0 0 11 11"><rect x="0" y="2" width="11" height="7" fill="#333"/><path d="M0 2l5.5 4L11 2" stroke="#fff" fill="none"/></svg>Email : hello@tuneroost.example</li>
</ul>
<div class="abs map" role="img" aria-label="Street map showing the office location"></div>

<h2 class="abs contact-title" style="left:695px;top:2802px">Contact Us</h2>
<div class="abs form">
  <div class="input">Name</div>
  <div class="input">Email</div>
  <div class="input">Subject</div>
  <div class="input message">Message</div>
</div>
<div class="abs verify"><div class="box"></div><span>I'm not a robot</span><div class="mark"></div></div>
<div class="abs submit">SUBMIT</div>

<!-- footer -->
<div class="abs footer-nav">Home<span>|</span>How TuneRoost Works<span>|</span>Why TuneRoost?<span>|</span>Venues<span>|</span>Artists<span>|</span>About TuneRoost<span>|</span>Contact</div>
<div class="abs copyright">Copyright © 2019 TuneRoost. All rights reserved.</div>
<div class="abs social" aria-label="Social links"><i></i><i></i><i></i><i></i></div>

</div>
</body>
</html>
```